Power Generation Company needs a stationary design

We need a design for our letter envelope, A4 Envelope and letterhead. Our company name is QELVANO Power which i attached here sample our our call card. We are based in the Philippines and is into the Power Generation business. We own power facilities like Hydropower plant, Solar Power Plant, Diesel Power Plant, Gas Turbine Power Plant. We sell our power to various electric distribution companies, factories and office buildings.

Target Market(s)

Electric Distribution Companies and Factories

Industry/Entity Type

It Company

Colors
ec1f27

Requirements
Must have
• Logo and company name
Nice to have
• No specific
Should not have
• No specific

```html
<!DOCTYPE html>
<html lang="en">
<head>
<meta charset="utf-8">
<title>QELVANO Power Envelope Set</title>
<link href="https://fonts.googleapis.com/css2?family=Open+Sans:wght@400;600;700&display=swap" rel="stylesheet">
<style>
  :root {
    --backdrop: #f399a4;
    --brand-red: #c8262d;
    --flap-red: #dc1638;
    --paper: #ffffff;
    --grey-text: #9a9a9a;
    --body-text: #555555;
    --label-red: #d3161f;
  }
  * { margin: 0; padding: 0; box-sizing: border-box; }
  html, body { width: 1200px; height: 957px; overflow: hidden; }
  body {
    position: relative;
    background: var(--backdrop);
    font-family: "Open Sans", Arial, sans-serif;
  }
  .envelope-art { position: absolute; left: 0; top: 0; }
  .brand-name {
    position: absolute;
    left: 248px; width: 174px; top: 264px;
    text-align: center;
    font-size: 23px; font-weight: 600;
    color: var(--brand-red);
    letter-spacing: 3px;
    line-height: 1;
  }
  .brand-tagline {
    position: absolute;
    left: 248px; width: 174px; top: 293px;
    text-align: center;
    font-size: 11.5px; font-weight: 700;
    color: var(--grey-text);
    letter-spacing: 0.8px;
    line-height: 1;
  }
  .contact-label {
    position: absolute;
    left: 292px; width: 85px; top: 757px;
    height: 10px;
    background: #e2e2e2;
    border-left: 2px solid var(--label-red);
    border-right: 2px solid var(--label-red);
    text-align: center;
    font-size: 6px; font-weight: 700;
    line-height: 10px;
    color: var(--label-red);
  }
  .contact-row {
    position: absolute;
    left: 166px; width: 338px;
    display: flex; align-items: center;
    font-size: 5.6px;
    line-height: 8px;
    color: var(--body-text);
    white-space: nowrap;
  }
  .contact-row.address { top: 771px; }
  .contact-row.lines { top: 782px; justify-content: space-between; }
  .contact-item { display: flex; align-items: center; gap: 3px; }
  .contact-icon { width: 7px; height: 7px; flex: none; }
</style>
</head>
<body>
<svg class="envelope-art" width="1200" height="957" viewBox="0 0 1200 957">
  <defs>
    <linearGradient id="ribbonGradient" x1="0" y1="0" x2="1" y2="0">
      <stop offset="0" stop-color="#8e0b1c"/>
      <stop offset="0.35" stop-color="#d0122f"/>
      <stop offset="0.65" stop-color="#e8204a"/>
      <stop offset="0.88" stop-color="#f26ea3"/>
      <stop offset="1" stop-color="#fbd3e2"/>
    </linearGradient>
    <linearGradient id="flapShade" x1="0" y1="0" x2="0" y2="1">
      <stop offset="0" stop-color="#dc1638"/>
      <stop offset="0.75" stop-color="#d51436"/>
      <stop offset="1" stop-color="#a40f24"/>
    </linearGradient>
    <filter id="softShadow" x="-5%" y="-5%" width="110%" height="110%">
      <feDropShadow dx="0" dy="1" stdDeviation="1.5" flood-color="#7a1f2c" flood-opacity="0.35"/>
    </filter>
  </defs>

  <g class="envelope-front" filter="url(#softShadow)">
    <rect x="133" y="274" width="403" height="530" fill="var(--paper)"/>
    <path role="img" aria-label="Red and pink abstract wave pattern across the flap"
          d="M133,274 L133,236 L144,168 Q147,152 163,152 L507,152 Q522,152 525,168 L536,236 L536,274 Z"
          fill="url(#ribbonGradient)"/>
    <rect role="img" aria-label="Red and pink abstract wave band along the bottom edge"
          x="133" y="778" width="403" height="26" fill="url(#ribbonGradient)"/>
  </g>
  <rect class="logo-tab" x="248" y="256" width="174" height="30" rx="6" fill="var(--paper)"/>
  <path class="footer-panel" d="M148,778 L522,778 L522,786 Q522,793 515,793 L155,793 Q148,793 148,786 Z" fill="var(--paper)"/>
  <line x1="172" y1="762" x2="292" y2="762" stroke="#c8c8c8" stroke-width="0.6"/>
  <line x1="377" y1="762" x2="500" y2="762" stroke="#c8c8c8" stroke-width="0.6"/>

  <g class="envelope-back" filter="url(#softShadow)">
    <rect x="610" y="236" width="403" height="568" fill="var(--paper)"/>
    <path d="M610,236 L621,168 Q624,152 640,152 L984,152 Q999,152 1002,168 L1013,236 Z" fill="url(#flapShade)"/>
    <rect role="img" aria-label="Red and pink abstract wave band along the bottom edge"
          x="610" y="766" width="403" height="38" fill="url(#ribbonGradient)"/>
  </g>
</svg>

<div class="brand-name">QELVANO</div>
<div class="brand-tagline">QELVANO Power Inc.</div>

<div class="contact-label">Contact Detail</div>

<div class="contact-row address">
  <span class="contact-item">
    <svg class="contact-icon" viewBox="0 0 10 10"><circle cx="5" cy="5" r="4.6" fill="none" stroke="#ec1f27" stroke-width="0.9"/><path d="M5,2.2 a1.8,1.8 0 0 1 1.8,1.8 c0,1.4 -1.8,3.6 -1.8,3.6 s-1.8,-2.2 -1.8,-3.6 A1.8,1.8 0 0 1 5,2.2z" fill="#ec1f27"/></svg>
    48 Meridian Trade Center, 220 Narra Ave., Sunfield Business Park, Sunfield, Laguna City, 4020 Philippines
  </span>
</div>

<div class="contact-row lines">
  <span class="contact-item">
    <svg class="contact-icon" viewBox="0 0 10 10"><circle cx="5" cy="5" r="4.6" fill="#ec1f27"/><rect x="2.6" y="3" width="4.8" height="4" rx="0.8" fill="#fff"/></svg>
    +632 555 0140
  </span>
  <span class="contact-item">
    <svg class="contact-icon" viewBox="0 0 10 10"><circle cx="5" cy="5" r="4.6" fill="#ec1f27"/><rect x="3" y="3" width="4" height="4" fill="#fff"/></svg>
    +632 555 0141
  </span>
  <span class="contact-item">
    <svg class="contact-icon" viewBox="0 0 10 10"><circle cx="5" cy="5" r="4.6" fill="none" stroke="#ec1f27" stroke-width="0.9"/><rect x="3.6" y="2.4" width="2.8" height="5.2" rx="0.5" fill="#ec1f27"/></svg>
    +63 917 555 0199
  </span>
  <span class="contact-item">
    <svg class="contact-icon" viewBox="0 0 10 10"><circle cx="5" cy="5" r="4.6" fill="#ec1f27"/><rect x="2.6" y="3.3" width="4.8" height="3.4" fill="#fff"/></svg>
    info@qelvano-pw.com
  </span>
  <span class="contact-item">
    <svg class="contact-icon" viewBox="0 0 10 10"><circle cx="5" cy="5" r="4.6" fill="#ec1f27"/><circle cx="5" cy="5" r="2.2" fill="none" stroke="#fff" stroke-width="0.8"/></svg>
    www.qelvano-pw.com
  </span>
</div>
</body>
</html>
```